Home page design for Drone video business (the Business focusses on home videos for realtors)

Dear reader,

*I NEED DESIGNS OF ALL THE PAGES*
We need a first design of a homepage and of 4 other pages of the website of a business that sells drone video services. All the pages will need to be in the similar design style.
The video's are targeted at consumers that want to sell there home and would like to have a cool drone video of photos of their home.

How does the website look:
- has a navbar on top
- A cool looking banner of an areal drone.
- A Big header: with company name: SkyLoftReels
- A smaller subheader: We film your home to increase your chances of sale
- Then a section with a Big header: How does it work
- In this section a place for a vimeo explainitory video
- Then a similar navbar styled bar with a phone number and a email address
- Then a section where the videos porfolio is displayed in a cool way
- Inside this sectiona header: Our work

- A section with header: Why us?
- 4 symbols here with a subheader and some lorum ipsum text underneath (see wireframe images)

- Under that a: Contact us
- where you can put in name, email, phone, message box and a send button

- At the bottom a footer with phone number and a fake address for now.

Be creative. Use creative but serious color.
Use a serious font. Make it a sharp design. Sharp lines. Not to dark design and not to light design.

The wireframes are the same kind of images.
PLEASE PUT IN DESIGNS OF ALL THE PAGES

Good luck

Target Market(s)

People that want to sell home and want to make a cool drone video or photos of their home.

Industry/Entity Type

Business

Contact Information for Business Card

Lucas Wenning
lucas@skyloftreels.example
+31647208351

Logo Text

SkyLoftReels

Number of Pages Required

1 page

Font styles to use
Sans Serif

Requirements
Must have
• All the sections as explained in the instructions.
• The nav bar should have an about us, services, portfolio and a contact us buttons.
• See instruction for details.
• Must include designs of the front page, contact us, our services, portfolio and contact us.
• If you do add some designs for the "about us", "services", "prices", "portfolio" and "contact us" pages, you make a way better chance of winning the competition.
Nice to have
• designs for the other pages as described at the Must haves. You make a better chance of winning if you include them. Look at the wireframes to see the mockups for those pages. think creative about what kind of sections and design should be included in those pages.
Should not have
• bad designs.

```html
<!DOCTYPE html>
<html lang="en">
<head>
<meta charset="utf-8">
<title>SkyLoftReels – Home</title>
<link href="https://fonts.googleapis.com/css2?family=Raleway:wght@300;400;600;700;800&family=Open+Sans:wght@400;600;700&display=swap" rel="stylesheet">
<style>
  :root{
    --red:#cf4647;
    --red-dark:#b83a3b;
    --ink:#3c3c3c;
    --muted:#7a7a7a;
    --white:#ffffff;
    --footer:#1e2227;
    --line:#e6e6e6;
  }
  *{box-sizing:border-box;margin:0;padding:0}
  html,body{width:1200px;height:3030px;overflow:hidden}
  body{font-family:"Open Sans",Arial,sans-serif;color:var(--ink);background:var(--white);position:relative}
  .heading{font-family:"Raleway",Arial,sans-serif;font-weight:700;font-size:33px;text-align:center;color:var(--ink)}

  /* Navigation */
  .site-nav{position:absolute;top:0;left:0;width:1200px;height:68px;background:var(--white);display:flex;align-items:center;padding:0 100px;z-index:2}
  .brand{display:flex;align-items:center;gap:10px;font-family:"Raleway",Arial,sans-serif;font-weight:700;font-size:22px;color:var(--ink)}
  .brand-dot{width:30px;height:30px;border-radius:50%;background:var(--red)}
  .nav-links{margin-left:auto;display:flex;gap:0;list-style:none}
  .nav-links li{font-family:"Raleway",Arial,sans-serif;font-size:11px;font-weight:600;text-transform:uppercase;color:var(--ink);margin-left:60px}

  /* Hero */
  .hero{position:absolute;top:68px;left:0;width:1200px;height:582px;overflow:hidden}
  .hero-photo{position:absolute;inset:0;background:linear-gradient(180deg,#5f6a6c 0%,#6e7866 45%,#4e6a36 75%,#3c5128 100%)}
  .hero-shade{position:absolute;inset:0;background:rgba(0,0,0,.18)}
  .hero-title{position:absolute;top:210px;width:100%;text-align:center;font-family:"Raleway",Arial,sans-serif;font-weight:300;font-size:50px;color:var(--white);letter-spacing:1px}
  .hero-title strong{font-weight:800}
  .hero-sub{position:absolute;top:278px;width:100%;text-align:center;font-family:"Raleway",Arial,sans-serif;font-weight:400;font-size:28px;color:var(--white)}
  .hero-arrow{position:absolute;top:270px;width:40px;height:40px;border:1px solid rgba(255,255,255,.45);border-radius:50%}
  .hero-arrow.prev{left:48px}
  .hero-arrow.next{right:48px}
  .hero-arrow svg{display:block;margin:11px auto}

  /* How it works */
  .how{position:absolute;top:650px;left:0;width:1200px;height:812px}
  .how .heading{position:absolute;top:62px;width:100%}
  .video{position:absolute;top:144px;left:99px;width:1002px;height:511px;overflow:hidden}
  .video-still{position:absolute;inset:0;background:radial-gradient(ellipse at 50% 35%,#f3c46a 0%,#d99a45 30%,#7a5a35 65%,#3a2e22 100%)}
  .play-ring{position:absolute;left:455px;top:150px;width:92px;height:92px;border:4px solid var(--white);border-radius:50%}
  .play-ring svg{position:absolute;left:30px;top:22px}
  .play-label{position:absolute;top:262px;width:100%;text-align:center;font-family:"Raleway",Arial,sans-serif;font-weight:300;font-size:54px;color:rgba(255,255,255,.55)}
  .video-bar{position:absolute;left:4px;right:4px;bottom:4px;height:24px;background:rgba(30,30,30,.8);display:flex;align-items:center;gap:8px;padding-right:8px}
  .video-bar .btn{width:42px;height:24px;background:rgba(60,60,60,.95);display:flex;align-items:center;justify-content:center}
  .video-bar .track{flex:1;height:8px;background:#5a5a5a}
  .video-bar .tag{width:80px;height:10px;background:#777}
  .contact-strip{position:absolute;top:690px;left:0;width:100%;display:flex;justify-content:center;gap:44px}
  .strip-item{display:flex;align-items:center;gap:16px;font-size:15px;color:var(--ink)}
  .strip-item b{color:var(--red);font-weight:700}
  .round-icon{width:62px;height:62px;border-radius:50%;background:var(--red);display:flex;align-items:center;justify-content:center;flex:none}

  /* Our work */
  .work{position:absolute;top:1462px;left:0;width:1200px;height:467px;background:var(--red)}
  .work .heading{position:absolute;top:56px;width:100%;color:var(--white)}
  .work-grid{position:absolute;top:134px;left:99px;display:flex;gap:33px}
  .work-card{width:312px;text-align:center}
  .work-thumb{position:relative;height:216px;box-shadow:0 6px 14px rgba(0,0,0,.3)}
  .work-thumb .ring{position:absolute;left:133px;top:85px;width:46px;height:46px;border:3px solid var(--white);border-radius:50%}
  .work-thumb .ring svg{position:absolute;left:15px;top:11px}
  .thumb-a{background:linear-gradient(135deg,#5b6b3e,#8fa24c 45%,#3a3e42)}
  .thumb-b{background:linear-gradient(180deg,#8fb3d6,#c9d8e6 55%,#6b7784)}
  .thumb-c{background:linear-gradient(180deg,#3a2a22,#c97a2e 55%,#1f1a17)}
  .work-caption{margin-top:28px;font-family:"Raleway",Arial,sans-serif;font-weight:700;font-size:12px;color:var(--white);text-transform:uppercase}

  /* Why us */
  .why{position:absolute;top:1929px;left:0;width:1200px;height:469px}
  .why .heading{position:absolute;top:68px;width:100%}
  .feature{position:absolute;display:flex;gap:22px;width:440px}
  .feature .round-icon{width:66px;height:66px}
  .feature h3{font-family:"Raleway",Arial,sans-serif;font-weight:700;font-size:16px;color:var(--ink);margin:4px 0 10px}
  .feature p{font-size:11.5px;line-height:21px;color:var(--muted)}
  .f1{left:128px;top:150px}.f2{left:627px;top:150px}
  .f3{left:128px;top:291px}.f4{left:627px;top:291px}

  /* Contact */
  .contact{position:absolute;top:2398px;left:0;width:1200px;height:577px;overflow:hidden}
  .contact-photo{position:absolute;inset:0;background:linear-gradient(180deg,#5c6874 0%,#46525d 45%,#3a4550 100%)}
  .contact-shade{position:absolute;inset:0;background:rgba(25,30,38,.55)}
  .contact .heading{position:absolute;top:84px;width:100%;color:var(--white)}
  .field{position:absolute;background:var(--white);border:none;font-family:"Open Sans",Arial,sans-serif;font-size:12px;color:#666;padding:12px 20px}
  .fn{left:214px;top:169px;width:362px;height:42px}
  .fe{left:214px;top:232px;width:362px;height:42px}
  .fp{left:214px;top:295px;width:362px;height:42px}
  .fm{left:600px;top:169px;width:360px;height:105px}
  .send{position:absolute;left:600px;top:295px;width:360px;height:42px;background:var(--red);color:var(--white);font-family:"Raleway",Arial,sans-serif;font-weight:700;font-size:15px;display:flex;align-items:center;justify-content:center}
  .info{position:absolute;top:397px;display:flex;align-items:center;gap:16px;color:var(--white);font-size:14px;line-height:24px}
  .info b{color:var(--red);font-weight:600}
  .i1{left:210px}.i2{left:537px}.i3{left:779px}

  /* Footer */
  .site-footer{position:absolute;top:2975px;left:0;width:1200px;height:55px;background:var(--footer);display:flex;align-items:center;padding:0 100px;color:#d6d6d6;font-size:10px}
  .social{margin-left:auto;display:flex;align-items:center;gap:20px}
  .social span.dot{width:10px;height:10px;border-radius:50%;background:#d6d6d6}
  .lang{margin-left:60px;color:#d6d6d6}
</style>
</head>
<body>

<nav class="site-nav">
  <div class="brand"><span class="brand-dot"></span>SkyLoftReels</div>
  <ul class="nav-links">
    <li>Home</li><li>Services</li><li>About Us</li><li>Portfolio</li><li>Contact</li>
  </ul>
</nav>

<header class="hero">
  <div class="hero-photo" role="img" aria-label="Photo of a camera drone in flight with its pilot holding a remote control on a grass field"></div>
  <div class="hero-shade"></div>
  <h1 class="hero-title">SKYLOFT <strong>REELS</strong></h1>
  <p class="hero-sub">We film your home to increase your chances of sale</p>
  <span class="hero-arrow prev"><svg width="10" height="16" viewBox="0 0 10 16"><path d="M8 1 2 8l6 7" fill="none" stroke="#fff" stroke-opacity=".6" stroke-width="1.5"/></svg></span>
  <span class="hero-arrow next"><svg width="10" height="16" viewBox="0 0 10 16"><path d="M2 1l6 7-6 7" fill="none" stroke="#fff" stroke-opacity=".6" stroke-width="1.5"/></svg></span>
</header>

<section class="how">
  <h2 class="heading">How does it work?</h2>
  <div class="video">
    <div class="video-still" role="img" aria-label="Video still of two drone operators preparing a drone in a field at sunset"></div>
    <span class="play-ring"><svg width="34" height="40" viewBox="0 0 34 40"><path d="M2 2l30 18L2 38z" fill="none" stroke="#fff" stroke-width="3" stroke-linejoin="round"/></svg></span>
    <div class="play-label">Play Video</div>
    <div class="video-bar">
      <span class="btn"><svg width="10" height="12" viewBox="0 0 10 12"><path d="M0 0l10 6-10 6z" fill="#fff"/></svg></span>
      <span class="track"></span>
      <span class="tag"></span>
    </div>
  </div>
  <div class="contact-strip">
    <div class="strip-item">
      <span class="round-icon"><svg width="22" height="22" viewBox="0 0 24 24"><path d="M6.6 10.8a15.1 15.1 0 0 0 6.6 6.6l2.2-2.2c.3-.3.7-.4 1-.2 1.1.4 2.3.6 3.6.6.6 0 1 .4 1 1V20c0 .6-.4 1-1 1A17 17 0 0 1 3 4c0-.6.4-1 1-1h3.5c.6 0 1 .4 1 1 0 1.3.2 2.5.6 3.6.1.3 0 .7-.2 1z" fill="#fff"/></svg></span>
      <span>Call Us : <b>+31640375219</b></span>
    </div>
    <div class="strip-item">
      <span class="round-icon"><svg width="24" height="18" viewBox="0 0 24 18"><rect x="0" y="0" width="24" height="18" rx="2" fill="#fff"/><path d="M1 2l11 8 11-8" fill="none" stroke="#cf4647" stroke-width="2"/></svg></span>
      <span>Email Us : <b>contact@skyloftreels.example</b></span>
    </div>
  </div>
</section>

<section class="work">
  <h2 class="heading">Our Work</h2>
  <div class="work-grid">
    <div class="work-card">
      <div class="work-thumb thumb-a" role="img" aria-label="Close-up of hands holding a drone remote control">
        <span class="ring"><svg width="16" height="20" viewBox="0 0 16 20"><path d="M1 1l14 9-14 9z" fill="none" stroke="#fff" stroke-width="2" stroke-linejoin="round"/></svg></span>
      </div>
      <p class="work-caption">Lorem ipsum is simply</p>
    </div>
    <div class="work-card">
      <div class="work-thumb thumb-b" role="img" aria-label="Drone flying between city high-rise buildings">
        <span class="ring"><svg width="16" height="20" viewBox="0 0 16 20"><path d="M1 1l14 9-14 9z" fill="none" stroke="#fff" stroke-width="2" stroke-linejoin="round"/></svg></span>
      </div>
      <p class="work-caption">Lorem ipsum is simply</p>
    </div>
    <div class="work-card">
      <div class="work-thumb thumb-c" role="img" aria-label="Drone silhouette over the sea at sunset">
        <span class="ring"><svg width="16" height="20" viewBox="0 0 16 20"><path d="M1 1l14 9-14 9z" fill="none" stroke="#fff" stroke-width="2" stroke-linejoin="round"/></svg></span>
      </div>
      <p class="work-caption">Lorem ipsum is simply</p>
    </div>
  </div>
</section>

<section class="why">
  <h2 class="heading">Why Us?</h2>
  <div class="feature f1">
    <span class="round-icon"><svg width="26" height="30" viewBox="0 0 26 30"><path d="M5 8h16l3 4v16H2V12z" fill="#fff"/><circle cx="13" cy="5" r="3" fill="none" stroke="#fff" stroke-width="2"/><text x="13" y="24" text-anchor="middle" font-family="Arial,sans-serif" font-weight="700" font-size="11" fill="#cf4647">%</text></svg></span>
    <div><h3>Cheap</h3><p>Lorem Ipsum is simply dummy text of the printing and typesetting industry. Lorem Ipsum has been the industry's standard dummy text ever since the 1500s</p></div>
  </div>
  <div class="feature f2">
    <span class="round-icon"><svg width="28" height="28" viewBox="0 0 28 28" fill="none" stroke="#fff" stroke-width="2.4"><path d="M3 3l8 8M25 3l-8 8M3 25l8-8M25 25l-8-8M3 10V3h7M18 3h7v7M3 18v7h7M25 18v7h-7"/></svg></span>
    <div><h3>Flexable</h3><p>Lorem Ipsum is simply dummy text of the printing and typesetting industry. Lorem Ipsum has been the industry's standard dummy text ever since the 1500s</p></div>
  </div>
  <div class="feature f3">
    <span class="round-icon"><svg width="26" height="32" viewBox="0 0 26 32"><path d="M7 18l-4 12 5-2 3 4 2-10M19 18l4 12-5-2-3 4-2-10" fill="#fff"/><circle cx="13" cy="11" r="10" fill="#fff"/><circle cx="13" cy="11" r="5" fill="none" stroke="#cf4647" stroke-width="2"/></svg></span>
    <div><h3>Quality</h3><p>Lorem Ipsum is simply dummy text of the printing and typesetting industry. Lorem Ipsum has been the industry's standard dummy text ever since the 1500s</p></div>
  </div>
  <div class="feature f4">
    <span class="round-icon"><svg width="28" height="26" viewBox="0 0 28 26" fill="none" stroke="#fff" stroke-width="2"><rect x="3" y="17" width="4" height="7"/><rect x="10" y="13" width="4" height="11"/><rect x="17" y="9" width="4" height="15"/><path d="M2 12L12 5l4 3 9-7M20 1h5v5"/></svg></span>
    <div><h3>Increase sale chance</h3><p>Lorem Ipsum is simply dummy text of the printing and typesetting industry. Lorem Ipsum has been the industry's standard dummy text ever since the 1500s</p></div>
  </div>
</section>

<section class="contact">
  <div class="contact-photo" role="img" aria-label="Aerial view of a city skyline with high-rise towers"></div>
  <div class="contact-shade"></div>
  <h2 class="heading">Contact us</h2>
  <div class="field fn">Name</div>
  <div class="field fe">Email</div>
  <div class="field fp">Phone</div>
  <div class="field fm">Message</div>
  <div class="send">SEND</div>
  <div class="info i1">
    <span class="round-icon"><svg width="18" height="24" viewBox="0 0 18 24"><path d="M9 0a9 9 0 0 0-9 9c0 6.5 9 15 9 15s9-8.5 9-15a9 9 0 0 0-9-9z" fill="#fff"/><circle cx="9" cy="9" r="3.2" fill="#cf4647"/></svg></span>
    <span>123 Street name, city name,<br>Coutry name : 365235</span>
  </div>
  <div class="info i2">
    <span class="round-icon"><svg width="22" height="22" viewBox="0 0 24 24"><path d="M6.6 10.8a15.1 15.1 0 0 0 6.6 6.6l2.2-2.2c.3-.3.7-.4 1-.2 1.1.4 2.3.6 3.6.6.6 0 1 .4 1 1V20c0 .6-.4 1-1 1A17 17 0 0 1 3 4c0-.6.4-1 1-1h3.5c.6 0 1 .4 1 1 0 1.3.2 2.5.6 3.6.1.3 0 .7-.2 1z" fill="#fff"/></svg></span>
    <span>Call Us :<br><b>+31640375219</b></span>
  </div>
  <div class="info i3">
    <span class="round-icon"><svg width="24" height="18" viewBox="0 0 24 18"><rect width="24" height="18" rx="2" fill="#fff"/><path d="M1 2l11 8 11-8" fill="none" stroke="#cf4647" stroke-width="2"/></svg></span>
    <span>Email Us :<br><b>contact@skyloftreels.example</b></span>
  </div>
</section>

<footer class="site-footer">
  <span>© Copyrights 2016. SkyLoftReels. All rights reserved.</span>
  <div class="social">
    <span>Connect with our social network :</span>
    <span class="dot"></span><span class="dot"></span><span class="dot"></span><span class="dot"></span><span class="dot"></span>
  </div>
  <span class="lang">CS</span>
</footer>

</body>
</html>
```